Business card design for a dynamic IT consulting company

We need a business card design for a young firm, specialized in the Telecommunications/Consulting industry. The name of the company is Quindor and Partners Business Consulting Ltd. (Short name: Quindor and Partnes)
Quindor = solve read reverse, so we aim to be uncomplicated and solution-oriented. The small pipe in our logo is also related to the word solve. So we need a new business card design, which is simple, eye catching and something non traditional (I would probably prefer a square shaped design rather than a rectangle, but open for suggestions). Attached our logo.

Target Market(s)

Usually our customers are Tier1 Telecoms providers (Q-Netra, Palorix, etc) and their executives.

Industry/Entity Type

Business

Contact Information for Business Card

Name: Bence Tolnavari
Email: b.tolnavari@quindor.hu
Web: www.quindor.hu
Mobile: +36 30 518 2769
Title: Managing Director

Optional:
Company name: Quindor and Partners Ltd.
Address: 1087 Budapest, Tolvenka str. 28/C, Hungary

Font styles to use
Other font styles liked:
• helveticaneue_medium, Prime Regular are used now.

Colors

Designer to choose colors to be used in the design.

Requirements
Must have
• I would like to have a 2 sided design.
Nice to have
• I thought if we make the logo a bit bigger (without the company name), that could go to the back with the company name below. I though, if the pipe in the logo is somehow touchable on the business card, would be nice and unique.

```html
<!DOCTYPE html>
<html lang="en">
<head>
<meta charset="utf-8">
<title>Quindor &amp; Partners – Business Card</title>
<link rel="stylesheet" href="https://fonts.googleapis.com/css2?family=Roboto:wght@300;400;500&display=swap">
<style>
  :root {
    --stage: #a9a9a9;
    --card-light: #ffffff;
    --card-dark: #1f1f1f;
    --ink: #3d3d3d;
    --ink-soft: #5a5a5a;
    --brand-blue: #1c7cc4;
    --brand-magenta: #b3279a;
    --icon-grey: #555555;
    --rule: #a8a8a8;
    --silver: #bcbcbc;
  }
  * { margin: 0; padding: 0; box-sizing: border-box; }
  html, body {
    width: 1200px;
    height: 1134px;
    overflow: hidden;
  }
  body {
    background: var(--stage);
    font-family: "Roboto", Arial, sans-serif;
    position: relative;
  }
  .card {
    position: absolute;
    top: 336px;
    width: 384px;
    height: 384px;
    border-radius: 14px;
  }
  .card--front {
    left: 192px;
    background: var(--card-light);
    text-align: center;
    color: var(--ink);
  }
  .card--back {
    left: 644px;
    background: var(--card-dark);
  }
  .wordmark {
    display: flex;
    align-items: center;
    justify-content: center;
    gap: 10px;
    font-weight: 300;
    letter-spacing: 0.2px;
  }
  .wordmark__square {
    width: 14px;
    height: 14px;
  }
  .card--front .wordmark {
    margin-top: 38px;
    font-size: 31px;
    color: var(--ink-soft);
  }
  .card--front .wordmark__square { background: var(--brand-magenta); }
  .holder {
    margin-top: 44px;
    font-size: 28px;
    font-weight: 500;
    line-height: 1.1;
  }
  .holder__first { color: var(--brand-blue); }
  .holder__last { color: var(--brand-magenta); font-weight: 400; }
  .holder-title {
    font-size: 18px;
    color: var(--ink-soft);
    margin-top: 3px;
  }
  .contact-icons {
    display: flex;
    justify-content: center;
    gap: 8px;
    margin-top: 23px;
  }
  .contact-icons svg { width: 20px; height: 20px; display: block; }
  .contact-lines {
    list-style: none;
    margin-top: 6px;
    font-size: 15.5px;
    line-height: 23px;
    color: var(--ink);
  }
  .divider {
    width: 100px;
    height: 2px;
    background: var(--rule);
    margin: 10px auto 13px;
  }
  .address {
    font-style: normal;
    font-size: 15.5px;
    line-height: 23px;
    color: var(--ink);
  }
  .card--back .wordmark {
    position: absolute;
    left: 0;
    right: 0;
    top: 50%;
    transform: translateY(-50%);
    flex-direction: column;
    gap: 22px;
    font-size: 34px;
    color: var(--silver);
  }
  .card--back .wordmark__square {
    width: 56px;
    height: 56px;
    background: var(--silver);
  }
</style>
</head>
<body>

<section class="card card--front" aria-label="Business card front">
  <div class="wordmark">
    <span class="wordmark__square"></span>
    <span class="wordmark__name">Quindor &amp; Partners</span>
  </div>

  <h1 class="holder">
    <span class="holder__first">Bence</span>
    <span class="holder__last">Tolnavari</span>
  </h1>
  <p class="holder-title">Managing Director</p>

  <div class="contact-icons" aria-hidden="true">
    <svg viewBox="0 0 20 20">
      <rect width="20" height="20" rx="3" fill="var(--brand-blue)"/>
      <path d="M6.2 4.5l2 2.1-1.1 1.5c.8 1.8 2 3 3.8 3.8l1.5-1.1 2.1 2-1.3 1.8C9 14.3 5.7 11 5 6.1z" fill="#fff"/>
    </svg>
    <svg viewBox="0 0 20 20">
      <rect width="20" height="20" rx="3" fill="var(--brand-magenta)"/>
      <rect x="4.5" y="6" width="11" height="8" rx="1" fill="#fff"/>
      <path d="M4.8 6.4l5.2 4 5.2-4" fill="none" stroke="var(--brand-magenta)" stroke-width="1.2"/>
    </svg>
    <svg viewBox="0 0 20 20">
      <rect width="20" height="20" rx="3" fill="var(--icon-grey)"/>
      <circle cx="10" cy="10" r="5.5" fill="none" stroke="#fff" stroke-width="1.3"/>
      <path d="M4.5 10h11M10 4.5c-2.2 3-2.2 8 0 11M10 4.5c2.2 3 2.2 8 0 11" fill="none" stroke="#fff" stroke-width="1"/>
    </svg>
  </div>

  <ul class="contact-lines">
    <li>+36 30 518 2769</li>
    <li>b.tolnavari@quindor.hu</li>
    <li>www.quindor.hu</li>
  </ul>

  <div class="divider"></div>

  <address class="address">
    1087 Budapest,<br>
    Tolvenka str. 28/C, Hungary
  </address>
</section>

<section class="card card--back" aria-label="Business card back">
  <div class="wordmark">
    <span class="wordmark__square"></span>
    <span class="wordmark__name">Quindor &amp; Partners</span>
  </div>
</section>

</body>
</html>
```